New Bicycle shop business card

Hi!
I'm looking for a business card for my new proffesional bike mechanics shop. This shop is only for fixing broken bikes and not selling bikes.
Peferbly a modern and sleek and modern design.
Colors: black, grey, red, white
Information:
Name: Rijwielwerkplaats Vanhoutte
Shop owner: Bart Vanhoutte & Marieke Segers
Website: www.rijwielwerkplaats-vanhoutte.be
Email: info@rijwielwerkplaats-vanhoutte.be
Phone number: +32471902368
Street adres: Kerkweg 46
9940 Bellebeke
Slogan/shop information: Herstellingen van alle merken.
Logo: see files.
Target Market(s)
People who seek a mechanic to fix or upgrade their bikes.
Contact Information for Business Card
Information:
Website: info@rijwielwerkplaats-vanhoutte.be
9940 Bellebeke
Logo: see files.

```html
<!DOCTYPE html>
<html lang="nl">
<head>
<meta charset="utf-8">
<title>Rijwielwerkplaats Vanhoutte – visitekaartje</title>
<link rel="stylesheet" href="https://fonts.googleapis.com/css2?family=Montserrat:wght@800&family=Open+Sans:wght@400;700&family=Kaushan+Script&family=Jost:wght@400&display=swap">
<style>
  :root {
    --stage: #2b2d31;
    --black: #0b0b0c;
    --charcoal: #3c3c3f;
    --steel: #5c5c5f;
    --silver: #b9b9bb;
    --silver-light: #d6d6d8;
    --white: #ffffff;
    --red: #e0202e;
    --ink: #1b1b1d;
    --muted: #6f6f73;
    --navy: #1f2f4a;
    --rule: #d9d9dc;
  }
  * { box-sizing: border-box; margin: 0; padding: 0; }
  html, body { width: 1200px; height: 900px; overflow: hidden; }
  body {
    background: var(--stage);
    display: flex;
    flex-direction: column;
    align-items: center;
    justify-content: center;
    gap: 40px;
  }
  .card {
    position: relative;
    width: 700px;
    height: 400px;
    border-radius: 24px;
    overflow: hidden;
    box-shadow: 0 14px 30px rgba(0,0,0,.45);
  }

  /* Back side */
  .card--back {
    background: linear-gradient(135deg, var(--black) 0%, #1c1c1e 45%, var(--steel) 100%);
  }
  .brand {
    position: absolute;
    display: flex;
    align-items: center;
    gap: 22px;
  }
  .brand__dot {
    flex: none;
    width: 64px;
    height: 64px;
    border-radius: 50%;
    background: var(--red);
  }
  .brand__name {
    font-family: "Montserrat", sans-serif;
    font-weight: 800;
    text-transform: uppercase;
    line-height: 1.1;
    white-space: nowrap;
  }
  .card--back .brand { left: 70px; top: 105px; }
  .card--back .brand__name { color: var(--white); font-size: 36px; letter-spacing: 1px; }
  .slogan-band {
    position: absolute;
    left: 0; right: 0; bottom: 0;
    height: 72px;
    background: linear-gradient(90deg, var(--steel) 0%, var(--silver) 55%, var(--silver-light) 100%);
    display: flex;
    align-items: center;
    padding-left: 60px;
  }
  .slogan {
    font-family: "Kaushan Script", cursive;
    font-size: 30px;
    color: var(--ink);
  }

  /* Front side */
  .card--front { background: var(--white); }
  .card--front .brand { left: 30px; top: 100px; width: 310px; gap: 14px; }
  .card--front .brand__dot { width: 48px; height: 48px; }
  .card--front .brand__name { color: var(--ink); font-size: 18px; letter-spacing: .3px; }
  .divider {
    position: absolute;
    left: 360px; top: 40px;
    width: 1px; height: 250px;
    background: var(--rule);
  }
  .contact {
    position: absolute;
    left: 384px; top: 56px;
    width: 300px;
    font-family: "Open Sans", sans-serif;
  }
  .contact__people {
    font-weight: 700;
    font-size: 15px;
    line-height: 1.45;
    color: var(--ink);
    padding-bottom: 10px;
    border-bottom: 2px solid var(--navy);
    width: 250px;
  }
  .contact__list { list-style: none; margin-top: 20px; }
  .contact__item {
    display: flex;
    align-items: center;
    gap: 10px;
    font-size: 13.5px;
    color: var(--muted);
    margin-bottom: 12px;
    white-space: nowrap;
  }
  .contact__icon { flex: none; width: 20px; height: 20px; }
  .address-band {
    position: absolute;
    left: 0; right: 0; bottom: 0;
    height: 72px;
    background: linear-gradient(90deg, var(--black) 0%, var(--charcoal) 60%, var(--steel) 100%);
    display: flex;
    align-items: center;
    padding-left: 40px;
  }
  .address {
    font-family: "Jost", sans-serif;
    font-size: 28px;
    color: var(--white);
  }
</style>
</head>
<body>

  <section class="card card--back" aria-label="Achterkant">
    <div class="brand">
      <span class="brand__dot"></span>
      <p class="brand__name">Rijwielwerkplaats<br>Vanhoutte</p>
    </div>
    <div class="slogan-band">
      <p class="slogan">Herstellingen van alle merken</p>
    </div>
  </section>

  <section class="card card--front" aria-label="Voorkant">
    <div class="brand">
      <span class="brand__dot"></span>
      <p class="brand__name">Rijwielwerkplaats<br>Vanhoutte</p>
    </div>
    <div class="divider"></div>
    <div class="contact">
      <p class="contact__people">Rijwielwerkplaats Vanhoutte<br>Shop owner: Bart Vanhoutte<br>&amp; Marieke Segers</p>
      <ul class="contact__list">
        <li class="contact__item">
          <svg class="contact__icon" viewBox="0 0 20 20" aria-hidden="true">
            <rect width="20" height="20" rx="3" fill="var(--navy)"/>
            <path d="M6 4.5l2 0 1 3-1.3 1a7 7 0 0 0 3.8 3.8l1-1.3 3 1 0 2c0 .8-.7 1.5-1.5 1.5A10 10 0 0 1 4.5 6c0-.8.7-1.5 1.5-1.5z" fill="#fff"/>
          </svg>
          +32471902368
        </li>
        <li class="contact__item">
          <svg class="contact__icon" viewBox="0 0 20 20" aria-hidden="true">
            <rect width="20" height="20" rx="3" fill="var(--navy)"/>
            <rect x="4" y="6" width="12" height="8.5" rx="1" fill="none" stroke="#fff" stroke-width="1.4"/>
            <path d="M4.5 6.5l5.5 4.5 5.5-4.5" fill="none" stroke="#fff" stroke-width="1.4"/>
          </svg>
          info@rijwielwerkplaats-vanhoutte.be
        </li>
        <li class="contact__item">
          <svg class="contact__icon" viewBox="0 0 20 20" aria-hidden="true">
            <rect width="20" height="20" rx="3" fill="var(--navy)"/>
            <circle cx="10" cy="10" r="5.8" fill="none" stroke="#fff" stroke-width="1.3"/>
            <ellipse cx="10" cy="10" rx="2.6" ry="5.8" fill="none" stroke="#fff" stroke-width="1.1"/>
            <path d="M4.2 10h11.6" stroke="#fff" stroke-width="1.1"/>
          </svg>
          www.rijwielwerkplaats-vanhoutte.be
        </li>
      </ul>
    </div>
    <div class="address-band">
      <p class="address">Kerkweg 46, 9940 Bellebeke</p>
    </div>
  </section>

</body>
</html>
```